"Got Radon?" Banner Ads

I need banner ads made for Brimwell Adspace Circuit campaign. There are 10 sizes of banners, so I need all 10 sizes. All of them can be similar in design and concept, but need to look good and the content must fill the space nicely.

The text on the ad is "Got Radon?" big/bold, and there should be a picture of a house with gas seeping into it from the ground. I have attached an example of an existing ad for reference.

These are the 10 sizes of banners that we need:
970x90
120x600
160x600
200x200
250x250
350x250
300x600
336x280
468x60
728x90

```html
<!DOCTYPE html>
<html lang="en">
<head>
<meta charset="utf-8">
<title>Got Radon? Banner Set</title>
<link href="https://fonts.googleapis.com/css2?family=Archivo+Black&family=Archivo+Narrow:wght@400&family=Arimo:wght@400&family=Montserrat:wght@700;800&display=swap" rel="stylesheet">
<style>
  :root {
    --forest: #0b4a05;
    --forest-mid: #2f6e1e;
    --panel-light: #7a9c70;
    --headline-yellow: #fff200;
    --ink: #000000;
    --paper: #ffffff;
    --label-green: #1c4a10;
    --photo-sky: #9fb7b8;
    --photo-siding: #b9c1bc;
    --photo-wood: #7a5a3e;
    --photo-lawn: #3d6a26;
  }
  * { margin: 0; padding: 0; box-sizing: border-box; }
  html, body { width: 1200px; height: 1000px; overflow: hidden; background: var(--paper); }
  .canvas { position: relative; width: 1200px; height: 1000px; }

  .brand-title {
    font-family: "Montserrat", sans-serif;
    font-weight: 800;
    color: var(--headline-yellow);
    -webkit-text-stroke: 2px var(--ink);
    paint-order: stroke fill;
    text-shadow: 1px 1px 0 var(--ink);
    line-height: 1;
    white-space: nowrap;
  }
  .brand-sub {
    font-family: "Montserrat", sans-serif;
    font-weight: 700;
    color: var(--paper);
    -webkit-text-stroke: 1.5px var(--ink);
    paint-order: stroke fill;
    line-height: 1;
    white-space: nowrap;
  }
  .offer-list {
    list-style: none;
    font-family: "Arimo", sans-serif;
    color: var(--paper);
    text-shadow: 2px 2px 4px rgba(0,0,0,0.85);
  }
  .cta {
    font-family: "Archivo Black", sans-serif;
    color: var(--headline-yellow);
    -webkit-text-stroke: 3px var(--ink);
    paint-order: stroke fill;
    text-shadow: 2px 2px 0 var(--ink);
    white-space: nowrap;
    line-height: 1;
  }
  .size-label {
    position: absolute;
    font-family: "Archivo Narrow", sans-serif;
    font-size: 24px;
    color: var(--label-green);
    transform: translateX(-50%);
  }
  .house-photo {
    background:
      linear-gradient(to bottom, var(--photo-sky) 0%, var(--photo-siding) 35%, var(--photo-wood) 62%, var(--photo-lawn) 85%, #4d5a2c 100%);
  }

  /* Leaderboard 970x90 */
  .leaderboard {
    position: absolute; left: 97px; top: 197px; width: 970px; height: 90px;
    background: var(--forest); display: flex;
  }
  .leaderboard .brand-block { width: 313px; padding: 20px 0 0 17px; }
  .leaderboard .brand-title { font-size: 24px; letter-spacing: 0.3px; }
  .leaderboard .brand-sub { font-size: 12.5px; margin-top: 6px; letter-spacing: 1px; }
  .leaderboard .offer-panel {
    width: 222px; padding: 7px 0 0 21px;
    background: linear-gradient(to right, var(--panel-light), var(--forest-mid));
  }
  .leaderboard .offer-list { font-size: 19px; line-height: 23.5px; }
  .leaderboard .house-photo { width: 168px; }
  .leaderboard .cta-block { flex: 1; position: relative; }
  .leaderboard .cta {
    position: absolute; left: 13px; top: 27px; font-size: 38px;
    transform: scaleX(0.84); transform-origin: left center;
  }

  /* Rectangle 600x300 */
  .rectangle {
    position: absolute; left: 282px; top: 520px; width: 600px; height: 300px;
    background: var(--forest); overflow: hidden;
  }
  .rectangle .house-photo { position: absolute; left: 130px; top: 0; width: 470px; height: 300px; }
  .rectangle .photo-fade {
    position: absolute; left: 130px; top: 0; width: 180px; height: 300px;
    background: linear-gradient(to right, var(--forest), rgba(11,74,5,0));
  }
  .rectangle .offer-band {
    position: absolute; left: 0; top: 105px; width: 240px; height: 92px;
    background: linear-gradient(to right, rgba(160,190,150,0.55), rgba(160,190,150,0.4) 80%, rgba(160,190,150,0));
  }
  .rectangle .brand-title { position: absolute; left: 19px; top: 22px; font-size: 34px; letter-spacing: 0.5px; }
  .rectangle .brand-sub { position: absolute; left: 21px; top: 62px; font-size: 16.5px; letter-spacing: 2.6px; }
  .rectangle .offer-list { position: absolute; left: 20px; top: 111px; font-size: 21px; line-height: 26px; }
  .rectangle .cta {
    position: absolute; left: 22px; top: 234px; font-size: 52px;
    transform: scaleX(0.85); transform-origin: left center;
  }
</style>
</head>
<body>
<main class="canvas">

  <section class="leaderboard" aria-label="970 by 90 banner">
    <div class="brand-block">
      <div class="brand-title">RADON REDUCTION</div>
      <div class="brand-sub">QUALITY MITIGATION SYSTEMS</div>
    </div>
    <div class="offer-panel">
      <ul class="offer-list">
        <li>FREE Estimates</li>
        <li>Same Day Service</li>
        <li>Best Price Guarantee</li>
      </ul>
    </div>
    <div class="house-photo" role="img" aria-label="Cutaway view of a two-storey house showing rooms and basement"></div>
    <div class="cta-block"><div class="cta">GOT RADON?</div></div>
  </section>
  <div class="size-label" style="left:582px; top:306px;">970X90</div>

  <section class="rectangle" aria-label="600 by 300 banner">
    <div class="house-photo" role="img" aria-label="Cutaway view of a two-storey house with basement, lawn and trees"></div>
    <div class="photo-fade"></div>
    <div class="offer-band"></div>
    <div class="brand-title">RADON REDUCTION</div>
    <div class="brand-sub">QUALITY MITIGATION SYSTEMS</div>
    <ul class="offer-list">
      <li>FREE Estimates</li>
      <li>Same Day Service</li>
      <li>Best Price Guarantee</li>
    </ul>
    <div class="cta">GOT RADON?</div>
  </section>
  <div class="size-label" style="left:577px; top:839px;">600X300</div>

</main>
</body>
</html>
```